Stylish Business Cards Wanted

- DOUBLE SIDED Design Required -

High end, edgy cards for a corporate and personal stylist. Must include logo,
Name: Belinda Harwick
Title: Director and Stylist
telephone : +61 8 7142 5809
email: belinda@theloombriefing.example
website: theloombriefing.example
Tag: Corporate Workwear & Uniform Specialist | Personal Stylist
Would like nice icons for telephone, email, website

Target Market(s)

Businesses wanting stylish uniforms, people wanting stylish wardrobes

Industry/Entity Type

Corporate Workwear Stylist

Contact Information for Business Card

I would like black, white and gold foiling incorporated in the design - possibly a touch of the other colours on my branding guide attached Name: Belinda Harwick Title: Director and Stylist telephone : +61 8 7142 5809 email: belinda@theloombriefing.example website: theloombriefing.example Tag: Corporate Workwear & Uniform Specialist | Personal Stylist Would like nice icons for telephone, email, website

Font styles to use
Other font styles liked:
• Raleway

Colors

Designer to choose colors to be used in the design.

Requirements
Must have
• Gold foil accents

```html
<!DOCTYPE html>
<html lang="en">
<head>
<meta charset="utf-8">
<title>The Loom Briefing – Business Cards</title>
<link rel="stylesheet" href="https://fonts.googleapis.com/css2?family=Questrial&family=Raleway:wght@300;400;600&display=swap">
<style>
  :root {
    --backdrop: #e8e8e9;
    --card-dark: #231f20;
    --card-light: #ffffff;
    --gold: #e2b84e;
    --ink: #231f20;
  }
  * { box-sizing: border-box; margin: 0; padding: 0; }
  html, body {
    width: 1200px;
    height: 507px;
    overflow: hidden;
  }
  body {
    background: var(--backdrop);
    position: relative;
    font-family: "Raleway", sans-serif;
  }
  .card {
    position: absolute;
    top: 106px;
    width: 493px;
    height: 295px;
  }
  .card--front { left: 83px; background: var(--card-dark); }
  .card--back { left: 624px; background: var(--card-light); }

  .brand-name {
    position: absolute;
    font-family: "Raleway", sans-serif;
    font-weight: 600;
    text-align: center;
    line-height: 1.05;
    letter-spacing: 0.02em;
  }
  .card--front .brand-name {
    left: 0; right: 0;
    top: 100px;
    font-size: 38px;
    color: var(--gold);
  }
  .card--back .brand-name {
    left: 40px;
    width: 150px;
    top: 118px;
    font-size: 25px;
    color: var(--ink);
  }

  .tagline {
    position: absolute;
    left: 0; right: 0;
    top: 205px;
    text-align: center;
    font-weight: 300;
    font-size: 12.2px;
    color: var(--gold);
    white-space: nowrap;
  }
  .tagline .sep { margin: 0 4px; }

  .divider {
    position: absolute;
    left: 197px;
    top: 93px;
    width: 1px;
    height: 109px;
    background: var(--ink);
  }
  .contact-block {
    position: absolute;
    left: 210px;
    top: 94px;
  }
  .person-name {
    font-family: "Questrial", sans-serif;
    font-size: 22px;
    color: var(--gold);
    line-height: 1;
  }
  .person-title {
    font-family: "Raleway", sans-serif;
    font-size: 11px;
    color: var(--ink);
    margin-top: 5px;
  }
  .contact-list { list-style: none; margin-top: 8px; }
  .contact-item {
    display: flex;
    align-items: center;
    height: 21px;
    font-family: "Questrial", sans-serif;
    font-size: 14.5px;
    color: var(--ink);
  }
  .contact-icon {
    width: 11px;
    height: 11px;
    margin-right: 6px;
    flex: none;
  }
</style>
</head>
<body>

<section class="card card--front" aria-label="Business card front">
  <div class="brand-name">The Loom<br>Briefing</div>
  <p class="tagline">Corporate Workwear<span class="sep">|</span>Uniform Specialist<span class="sep">|</span>Personal Stylist</p>
</section>

<section class="card card--back" aria-label="Business card back">
  <div class="brand-name">The Loom<br>Briefing</div>
  <div class="divider"></div>
  <div class="contact-block">
    <h1 class="person-name">Belinda Harwick</h1>
    <p class="person-title">Director and Stylist</p>
    <ul class="contact-list">
      <li class="contact-item">
        <svg class="contact-icon" viewBox="0 0 12 12" aria-hidden="true">
          <circle cx="6" cy="6" r="6" fill="var(--gold)"/>
          <path d="M3 5.2c0-1 1-1.6 3-1.6s3 .6 3 1.6l-1 .3-.3-.8H4.3L4 5.5z M4.2 6h3.6l.6 2.4H3.6z" fill="#fff"/>
        </svg>
        +61 8 7142 5809
      </li>
      <li class="contact-item">
        <svg class="contact-icon" viewBox="0 0 12 12" aria-hidden="true">
          <circle cx="6" cy="6" r="6" fill="var(--gold)"/>
          <rect x="3" y="4" width="6" height="4.2" fill="#fff"/>
          <path d="M3 4l3 2.4L9 4" fill="none" stroke="var(--gold)" stroke-width="0.8"/>
        </svg>
        belinda@theloombriefing.example
      </li>
      <li class="contact-item">
        <svg class="contact-icon" viewBox="0 0 12 12" aria-hidden="true">
          <circle cx="6" cy="6" r="6" fill="var(--gold)"/>
          <g fill="none" stroke="#fff" stroke-width="0.7">
            <circle cx="6" cy="6" r="3.3"/>
            <ellipse cx="6" cy="6" rx="1.4" ry="3.3"/>
            <path d="M2.7 6h6.6M3.2 4.4h5.6M3.2 7.6h5.6"/>
          </g>
        </svg>
        theloombriefing.example
      </li>
    </ul>
  </div>
</section>

</body>
</html>
```